Looking for a dynamic business card for a pizzeria.

A business card with our food, logo, and space for name, title, email, website, phone. The card should convey quality, unique, amazing. On the front, I envision food photo or photos with the owners names and contact information. On the back, more food with locations, website, facebook, twitter, instagram icons. It should look polished, not cartoonish, or plain.
Target Market(s)
upscale, local food buyers, 30-50 years in age.
Industry/Entity Type
Restaurant
Contact Information for Business Card
Business Name: Bru'nettix, LLC
Website: www.brunettix.com
Back:
2 locations: (can list on the back of card)
1. Harborview
4087 Corlan Avenue
Larkford, WA 98410
360-481-5067
2. Cedar Ridge
7315 Wendmere Road
Larkford, WA 98412
360-293-8840
front:
EDITABLE space for
Business name
Person's Name
title
2nd title
Email address
cell-phone number
Requirements
Must have
- logo
- my food photo or photos (no watermarks showing)
- locations on back
- Person contact information on front
- full bleed

```html
<!DOCTYPE html>
<html lang="en">
<head>
<meta charset="utf-8">
<title>Bru'nettix business card</title>
<link rel="stylesheet" href="https://fonts.googleapis.com/css2?family=Arimo:wght@400;700&display=swap">
<style>
  :root {
    --page: #e9e5dd;
    --green: #1f5a2c;
    --green-dark: #123a1c;
    --green-text: #2e6b35;
    --red: #c0161c;
    --ink: #1d1d1d;
    --paper: #ffffff;
    --rule: #9a9a9a;
    --back-ink: #e8ece8;
  }
  * { box-sizing: border-box; margin: 0; padding: 0; }
  html, body {
    width: 1200px; height: 950px; overflow: hidden;
    background: var(--page);
    font-family: "Arimo", Arial, sans-serif;
  }
  .canvas {
    width: 1200px; height: 950px;
    display: flex; flex-direction: column; align-items: center; justify-content: center; gap: 30px;
  }
  .card {
    position: relative; width: 760px; height: 434px; overflow: hidden;
    box-shadow: 0 6px 18px rgba(0,0,0,.18);
  }

  /* Back side */
  .card-back {
    background: linear-gradient(135deg, var(--green) 0%, var(--green-dark) 100%);
    color: #fff;
  }
  .back-brand {
    position: absolute; left: 0; right: 0; top: 172px;
    display: flex; justify-content: center; align-items: center; gap: 18px;
  }
  .back-brand-name { font-size: 56px; font-weight: 700; letter-spacing: 2px; color: var(--back-ink); white-space: nowrap; }
  .back-brand-mark { width: 68px; height: 68px; border-radius: 50%; background: var(--back-ink); flex: none; }
  .back-website {
    position: absolute; left: 0; right: 0; top: 262px; text-align: center;
    font-size: 18px; letter-spacing: 5px; color: #cfd8cf;
  }
  .back-social { position: absolute; right: 28px; top: 24px; display: flex; gap: 12px; }
  .back-social span { width: 18px; height: 18px; border-radius: 50%; background: var(--red); }

  /* Front side */
  .card-front { background: var(--paper); color: var(--ink); }
  .swoosh { position: absolute; inset: 0; }
  .person { position: absolute; left: 40px; top: 40px; }
  .person-name { font-size: 24px; font-weight: 700; letter-spacing: 1px; color: var(--green-dark); }
  .person-title { font-size: 17px; color: var(--red); margin-top: 4px; }
  .front-brand {
    position: absolute; right: 40px; top: 34px;
    display: flex; align-items: center; gap: 12px;
  }
  .front-brand-name { font-size: 46px; font-weight: 700; letter-spacing: 1px; color: var(--green-text); white-space: nowrap; }
  .front-brand-mark { width: 62px; height: 62px; border-radius: 50%; background: var(--red); flex: none; }
  .rule { position: absolute; left: 40px; right: 40px; top: 108px; height: 1px; background: var(--rule); }
  .location { position: absolute; font-size: 18px; line-height: 22px; font-style: normal; }
  .location .area { color: var(--green-text); font-size: 16px; }
  .location .label { color: var(--green-text); }
  .loc-harborview { left: 40px; top: 124px; }
  .loc-cedar { left: 280px; top: 168px; }
  .contact { position: absolute; left: 500px; top: 240px; list-style: none; font-size: 18px; line-height: 30px; }
  .contact li { display: flex; align-items: center; gap: 12px; }
  .contact svg { width: 16px; height: 16px; fill: var(--green-dark); flex: none; }
</style>
</head>
<body>
<main class="canvas">

  <section class="card card-back" aria-label="Card back">
    <div class="back-social"><span></span><span></span></div>
    <div class="back-brand">
      <span class="back-brand-name">BRU'NETTIX</span>
      <span class="back-brand-mark"></span>
    </div>
    <p class="back-website">www.brunettix.com</p>
  </section>

  <section class="card card-front" aria-label="Card front">
    <svg class="swoosh" viewBox="0 0 760 434" preserveAspectRatio="none" aria-hidden="true">
      <path d="M0,282 C180,350 430,392 760,404 L760,410 C430,400 180,362 0,298 Z" fill="var(--red)"/>
      <path d="M0,306 C180,370 430,404 760,414 L760,434 L0,434 Z" fill="var(--green)"/>
    </svg>

    <div class="person">
      <p class="person-name">MARCO DELANE</p>
      <p class="person-title">President</p>
    </div>

    <div class="front-brand">
      <span class="front-brand-name">BRU'NETTIX</span>
      <span class="front-brand-mark"></span>
    </div>

    <div class="rule"></div>

    <address class="location loc-harborview">
      <div class="area">Harborview</div>
      <div>4087 Corlan Avenue</div>
      <div>Larkford, WA 98410</div>
      <div><span class="label">Phone:</span>360-481-5067</div>
    </address>

    <address class="location loc-cedar">
      <div class="area">Cedar Ridge</div>
      <div>7315 Wendmere Road</div>
      <div>Larkford, WA 98412</div>
      <div><span class="label">Phone:</span>360-293-8840</div>
    </address>

    <ul class="contact">
      <li><svg viewBox="0 0 16 16"><path d="M4 0h8a1 1 0 0 1 1 1v14a1 1 0 0 1-1 1H4a1 1 0 0 1-1-1V1a1 1 0 0 1 1-1zm1 2v10h6V2zm3 11a1 1 0 1 0 0 2 1 1 0 0 0 0-2z"/></svg>360-512-7746</li>
      <li><svg viewBox="0 0 16 16"><path d="M0 3h16v10H0zm1 1.2V12h14V4.2L8 9z"/></svg>name@brunettix.com</li>
      <li><svg viewBox="0 0 16 16"><circle cx="8" cy="8" r="7.5"/></svg>www.brunettix.com</li>
    </ul>
  </section>

</main>
</body>
</html>
```